Web design for small empirical brand consulting company that will sell a web-based brand tool

We need a totally new and very appealing website:
Purpose: We want to attract lots of potential customers with this website... especially, we want to sell our web-based tool valuquant®... we want to be perceived as innovative, trendy, but solid and reliable… we want customers go to the website, login at „valuquant®“ (see structure), and perceive how it works.. and the contacting us or in the near future being able to buy a login and work with the tool… so we want to a) inform (on the website or send the url to customers) and b) to „force“ potential customers getting in contact with us…
Structure (e.g.): Must Home, valuquant®, About us, Contact (incl. legal notice); we are open for more, Nice to have e.g. references/clients, press... for example, we publish a nice book in a couple of months and might want to show it somewhere on the website as well...)
Layout: We would like to have more/mainly figures - may be animated or something like that – in specific those on slides 7 and 8 as well as 6 and 9 (which would be for our web-based tool valuquant®...)... excellent, but simple and with few text…
Fonts: Eurostile; CMYK 100/23/100/19, CMYK 0/0/0/70
Logo: Would you please use the lorentavo-logo used in this file?
Social Media: we think that it might make sense to be connected to chatterbay, quipline and so on as well…
Phantasy: May be it is possible to have something between a classic marketing research and an e-commerce website... just a thought... because it is mainly about the new tool that will be assessable through a login... but customers might want to contact us or vice versa in order to check how the tool will work (btw: you do not have further info about valuquant® here... I know)… I dream of having a site where people go to and by components of our tool like at brimbo… click and buy and go for it…
It is possible to program it in php or java? Thanks.
Pages I personally like: Don’t know if that helps, but I personally like those websites just they seem so simple: http:// www.pellivarn.com/, http://www.craftelune.net/... but I am veeery open
Pages I do not like anymore: my own www.lorentavo.ch

```html
<!DOCTYPE html>
<html lang="en">
<head>
<meta charset="utf-8">
<title>lorentavo – valuquant®</title>
<link href="https://fonts.googleapis.com/css2?family=Jura:wght@400;600;700&family=Arimo:wght@400;700&display=swap" rel="stylesheet">
<style>
  :root{
    --green:#00793d;
    --green-dark:#006433;
    --ink:#4d4d4d;
    --muted:#8a8a8a;
    --pale:#f6f6f8;
    --row:#ececec;
    --dark:#333333;
    --darker:#262626;
    --white:#ffffff;
  }
  *{margin:0;padding:0;box-sizing:border-box}
  html,body{width:912px;height:1200px;overflow:hidden;background:var(--white)}
  body{position:relative;font-family:"Jura",sans-serif;color:var(--ink)}
  .abs{position:absolute}

  /* header */
  .site-header{top:0;left:0;width:912px;height:41px;background:var(--white);box-shadow:0 1px 2px rgba(0,0,0,.08)}
  .brand{left:228px;top:12px;font-size:17px;font-weight:600;color:var(--ink);display:flex;align-items:center;gap:5px}
  .brand-mark{width:6px;height:13px;background:var(--green)}
  .nav{top:16px;font-size:8px;color:var(--ink)}
  .login-btn{left:631px;top:10px;width:43px;height:20px;background:var(--green);color:var(--white);font:700 7px "Arimo",sans-serif;display:flex;align-items:center;justify-content:center;border-radius:2px}

  /* hero */
  .hero{top:41px;left:0;width:912px;height:241px;background:linear-gradient(100deg,#3a2a1c 0%,#8a6a44 30%,#c9a878 50%,#6b5a48 72%,#2c2620 100%)}
  .hero-title{left:228px;top:120px;width:220px;font-size:12px;line-height:15px;color:var(--white);font-weight:600}
  .btn{height:19px;font:700 6.5px "Arimo",sans-serif;display:flex;align-items:center;justify-content:center;border-radius:2px;letter-spacing:.2px}
  .btn-grey{background:#555;color:var(--white)}
  .btn-white{background:var(--white);color:var(--ink)}

  /* intro */
  .intro{top:282px;left:0;width:912px;height:102px;background:var(--pale)}
  .intro-bar{left:228px;top:301px;width:26px;height:3px;background:var(--ink)}
  .intro-line{left:228px;top:310px;font-size:8.5px;color:var(--muted)}
  .intro-line b{color:var(--green);font-weight:700}
  .intro-line .name{color:var(--ink)}
  .intro-sub{left:228px;top:325px;font-size:6px;color:var(--ink)}

  /* measure */
  .section-title{font-size:11px;color:var(--ink);font-weight:600}
  .measure-text{left:228px;top:441px;width:115px;font-size:6.2px;line-height:9px;color:var(--muted)}
  .category{width:89px}
  .category-head{height:28px;background:var(--green);color:var(--white);font-size:8px;display:flex;align-items:center;justify-content:center;border-radius:3px}
  .category-list{margin-top:3px;height:101px;border:2px solid var(--green);border-radius:3px;padding:2px 2px}
  .category-list li{list-style:none;height:20px;margin-bottom:3.5px;background:var(--row);color:var(--green);font-size:8px;display:flex;align-items:center;justify-content:center}

  /* benefits */
  .benefits{top:594px;left:0;width:912px;height:148px;background:var(--green)}
  .benefits-text{top:50px;left:0;width:912px;text-align:center;font-size:8.5px;line-height:11px;color:var(--white)}
  .learn-btn{left:413px;top:95px;width:78px;height:23px;border:1px solid #2f9a60;color:#4fb47c;font-size:7px;display:flex;align-items:center;justify-content:center}

  /* features */
  .features-title{top:770px;left:0;width:912px;text-align:center;font-size:10.5px;color:var(--ink)}
  .feature{width:110px;text-align:center;top:805px}
  .feature svg{display:block;margin:0 auto}
  .feature h3{margin-top:10px;font-size:8.5px;color:var(--green);font-weight:600}
  .feature p{margin-top:6px;font-size:6.2px;line-height:8px;color:var(--ink)}

  /* footer */
  .site-footer{top:936px;left:0;width:912px;height:264px;background:var(--dark)}
  .press-title{left:228px;top:963px;font-size:10px;color:var(--white);font-weight:600}
  .press-text{left:228px;top:990px;width:208px;font-size:6.5px;line-height:8.5px;color:#cfcfcf}
  .press-more{left:228px;top:1031px;font-size:6.5px;color:#cfcfcf}
  .press-image{left:451px;top:966px;width:223px;height:82px;background:linear-gradient(120deg,#dfe7ef 0%,#a8b4c2 35%,#e9dfc7 60%,#7f8a98 100%)}
  .tweet-bar{left:228px;top:1068px;width:446px;height:26px;background:var(--darker);display:flex;align-items:center;padding-left:14px;gap:15px;font-size:5.5px;color:#cfcfcf}
  .tweet-bar a{color:#4aa8e0;text-decoration:none}
  .tweet-dot{width:9px;height:9px;border-radius:50%;background:#4aa8e0}
  .footer-brand{left:228px;top:1110px;font-size:13px;font-weight:600;color:var(--white);display:flex;align-items:center;gap:4px}
  .footer-brand .brand-mark{width:4px;height:10px;background:#aaa}
  .copyright{left:228px;top:1135px;font-size:5.5px;color:#cfcfcf}
  .social{left:614px;top:1133px;display:flex;gap:10px}
  .social span{width:8px;height:8px;border-radius:50%;background:#9a9a9a}
  .footer-rule{left:228px;top:1150px;width:446px;height:1px;background:#555}
  .footer-note{left:228px;top:1157px;width:446px;font-size:4.6px;line-height:6.5px;color:#9a9a9a}
</style>
</head>
<body>

<header class="abs site-header">
  <div class="abs brand"><span class="brand-mark"></span>lorentavo</div>
  <nav>
    <span class="abs nav" style="left:405px">About lorentavo</span>
    <span class="abs nav" style="left:477px">valuquant®</span>
    <span class="abs nav" style="left:541px">About us</span>
    <span class="abs nav" style="left:584px">Contact Us</span>
  </nav>
  <div class="abs login-btn">LOGIN</div>
</header>

<section class="abs hero" role="img" aria-label="Photo of a desk with a smartphone, a tablet, a pen and sketched planning notes"></section>
<h1 class="abs hero-title">valuquant®: Simply measuring and modeling your brand success</h1>
<div class="abs btn btn-grey" style="left:228px;top:175px;width:62px">TAKE A TOUR</div>
<div class="abs btn btn-white" style="left:300px;top:175px;width:62px">DEMO LINK</div>

<section class="abs intro"></section>
<div class="abs intro-bar"></div>
<p class="abs intro-line"><span class="name">lorentavo</span>: We measure, <b>test and model your brand</b> and your success</p>
<p class="abs intro-sub">lorentavo ltd., a spin-off company from the University of Veldmark, specializes in empirical brand consulting</p>
<div class="abs btn btn-grey" style="left:228px;top:347px;width:52px">READ MORE</div>

<h2 class="abs section-title" style="left:228px;top:413px">lorentavo: If you can't measure it, you can't manage it</h2>
<p class="abs measure-text">Using our unique, scientifically tested instruments, lorentavo measures and models your brand, so you can effectively and successfully manage it</p>

<div class="abs category" style="left:377px;top:444px">
  <div class="category-head">COMPANY BRAND</div>
  <ul class="category-list"><li>Path finder</li><li>Innovator</li><li>---</li><li>---</li></ul>
</div>
<div class="abs category" style="left:481px;top:444px">
  <div class="category-head">PRODUCT SERVICE</div>
  <ul class="category-list"><li>Attractivity</li><li>---</li><li>---</li><li>---</li></ul>
</div>
<div class="abs category" style="left:584px;top:444px">
  <div class="category-head">CEO BRAND</div>
  <ul class="category-list"><li>Leadership</li><li>Enterprenurship</li><li>---</li><li>---</li></ul>
</div>

<section class="abs benefits">
  <p class="abs benefits-text">Benefits: More successful market development and activities through sound<br>brand analysis and trend modeling using valuquant®</p>
  <div class="abs learn-btn">LEARN MORE &gt;&gt;</div>
</section>

<h2 class="abs features-title">Using valuquant® forsters</h2>

<div class="abs feature" style="left:211px">
  <svg width="44" height="44" viewBox="0 0 44 44"><circle cx="22" cy="22" r="20.5" fill="none" stroke="#00793d" stroke-width="1.5"/><circle cx="18" cy="22" r="6" fill="none" stroke="#444" stroke-width="2"/><circle cx="26" cy="22" r="6" fill="none" stroke="#444" stroke-width="2"/></svg>
  <h3>Closeness</h3><p>valuquant® lets you get even closer to your target groups.</p>
</div>
<div class="abs feature" style="left:340px">
  <svg width="44" height="44" viewBox="0 0 44 44"><circle cx="22" cy="22" r="20.5" fill="none" stroke="#00793d" stroke-width="1.5"/><rect x="13" y="24" width="3" height="6" fill="#333"/><rect x="18" y="21" width="3" height="9" fill="#333"/><rect x="23" y="18" width="3" height="12" fill="#333"/><rect x="28" y="14" width="3" height="16" fill="#333"/><path d="M12 22 L30 12" stroke="#333" stroke-width="1.2"/></svg>
  <h3>Security</h3><p>valuquant® makes opinions and attitudes immediately visual.</p>
</div>
<div class="abs feature" style="left:455px">
  <svg width="44" height="44" viewBox="0 0 44 44"><circle cx="22" cy="22" r="20.5" fill="none" stroke="#00793d" stroke-width="1.5"/><rect x="12" y="25" width="20" height="4" fill="#333"/><path d="M15 25 L22 15 L29 25 Z" fill="#333"/></svg>
  <h3>Fit</h3><p>valuquant® allows a custom-fit communication</p>
</div>
<div class="abs feature" style="left:567px">
  <svg width="44" height="44" viewBox="0 0 44 44"><circle cx="22" cy="22" r="20.5" fill="none" stroke="#00793d" stroke-width="1.5"/><path d="M13 22 L19 28 L31 15" fill="none" stroke="#333" stroke-width="4"/></svg>
  <h3>Customer Loyality</h3><p>valuquant® supports the bond to your customer base.</p>
</div>

<footer class="abs site-footer"></footer>
<h2 class="abs press-title">press release</h2>
<p class="abs press-text">Added value: valuquant® provides a means to be closer to your customers, more security, more precise communication – all of which means more success</p>
<span class="abs press-more">read more..</span>
<div class="abs press-image" role="img" aria-label="Photo of a pocket watch with a world map dial resting on banknotes"></div>
<div class="abs tweet-bar"><span class="tweet-dot"></span><span>Lorem Ipsum is simply dummy text of the printing and typesetting industry <a>http://t.co/4kqfp2w</a></span></div>
<div class="abs footer-brand"><span class="brand-mark"></span>lorentavo</div>
<p class="abs copyright">Copyright All Right Reserved lorentavo 2014 &nbsp; Privacy Policy &nbsp;|&nbsp; Sitemap</p>
<div class="abs social" aria-label="chatterbay, quipline and other networks"><span></span><span></span><span></span><span></span></div>
<div class="abs footer-rule"></div>
<p class="abs footer-note">Lorentavo builds valuquant® to turn brand perception into clear numbers. Our team combines empirical research, sound statistics and careful consulting so that every decision rests on solid data. Clients use the tool to test ideas, track positioning and model the effect of campaigns before they spend a budget. Ask for a demo login and see how measuring your brand becomes part of everyday management work, simple and reliable.</p>

</body>
</html>
```